Field Basket - Store need a label design

We need a Label Design for our Cosmetic Line with Hemp Cosmetics. We do not want a hemp leaf on our design. We want our LOGO infront of the design with the name of the product (shower gel, body lotion, .....) The ingredients must be included as well as in the bottle within 12 months. The font is smaller than 3mm. Generally, the font must be at least 2mm in size. What we need: 100x140mm 200ml E 12m 4x as: Hemp - shampoo, shower gel, body lotion and hair balm 20x66 mm 50g E (2 pieces for front and back) as: face cream, hand cream 42x52mm as: lip balm (sample how it should look in the uploaded files with the name morvil) What else should be on it: WITHOUT artificial colors and fragrances WITHOUT paraffins WITHOUT silicones with pure hemp seed oil Product not tested on animals Manufacturer: MORVIL A-4812 GRUNDLACH Description: HANF-SHAMPOO 200 ml Skin-mild washing-active ingredients develop a particularly pleasant and gentle cleansing effect. High-quality hemp seed oil nourishes the hair in a natural way and makes it pleasantly soft, loose and supple. BRISK MEADOW- is suitable for all hair types, especially for damaged and dull hair. HEMP SHOWER BATH 200 ml The pleasant foam cleans mildly and gently. The excellent care effect of natural hemp seed oil makes skin and hair pleasantly soft and supple.BRISK MEADOW- is suitable for mild cleansing and care, especially of sensitive skin and damaged hair. HEMP-FOAM BATH 200 ml Skin-mild washing-active ingredients develop a particularly mild and creamy foam. The excellent care effect of natural hemp seed oil makes the skin exceptionally soft and supple.BRISK MEADOW- is suitable for mild cleansing and care, especially of sensitive, rough and chapped skin. HEMP HAIR BALM 200 ml A special combination of natural hemp seed oil and other high-quality vegetable oils cares for the hair perfectly and makes it pleasantly soft, loose, supple, naturally shiny, extremely easy to style and effectively prevents the cleavage of the tips. BRISK MEADOW HEMP HAIR BALM is suitable for all hair types, especially for damaged, damaged, brittle and dull hair, as well as split hair tips. HEMP BODY LOTION 200 ml Pure Hemp Seed Oil nourishes the skin naturally, prevents it from drying out too much and makes it particularly soft and supple.BRISK MEADOW HEMP BODY LOTION is for pleasant body care, especially after bathing, especially in dry, brittle and sensitive skin HEMP FACE CREAM 50 g The particularly high content of pure hemp seed oil nourishes the skin perfectly and makes it unusually soft and supple.BRISK MEADOW HEMP FACE CREAM is suitable for pleasant and moisturizing care of the entire face, especially for dry and brittle skin Skin. HEMP HAND CREAM 50 g The high content of pure hemp seed oil and natural beeswax protects and nourishes the skin perfectly and makes it soft and supple. BRISK MEADOW HEMP HAND CREAM is suitable for protective care especially of stressed, sensitive and brittle skin. HEMP LIP BALM 6 g Natural hemp seed oil, pure beeswax and other valuable ingredients provide long-lasting care for the lips and protect them from adverse weather conditions and dehydration.BRISK MEADOW HEMP LIP BALM is particularly suitable for the lasting care of sensitive, brittle and torn lips. HANF-SHAMPOO Ingredients (INCI): Aqua, Sodium Laureth Sulfate, TEA-Lauryl Sulfate, Disodium Laureth Sulfosuccinate, Potassium Cocoyl Hydrolized Collagen, Linoleamide-DEA, Cannabis Sativa Seed Oil, Natural Perfume, Sodium Chloride, Citric Acid, Potassium Sorbate, Panthenol , Tocopherol, chlorophyll, citral *, citronellol *, geraniol *, limonene *, linalool *. (* natural ingredients of essential oils). HEMP-DUSCHBAD Ingredients (INCI): Aqua, Sodium Laureth Sulfate, TEA-Lauryl Sulfate, Disodium Laureth Sulfosuccinate, Potassium Cocoyl Hydrolized Collagen, Cocoamphodiacetate, Linoleamide-DEA, Cocamidopropylamine Oxide, Cannabis Sativa Seed Oil, Natural Perfume, Coco-Glucoside, Glyceryl Oleate, Sodium Chloride, Citric Acid, Potassium Sorbate, Panthenol, Tocopherol, Chlorophyll, Citral *, Citronellol *, Geraniol *, Limonene *, Linalool *. (* natural ingredients of essential oils). HANF-SCHAUMBAD Ingredients (INCI): Aqua, MIPA-Pareth-25-Sulfate, Cocamidopropyl Betaine, Disodium Laureth Sulfosuccinate, Linoleamide-DEA, Cannabis Sativa Seed Oil, Coco-Glucoside, Glyceryl Oleate, Natural Perfume, Panthenol, Potassium Sorbate, Citric Acid, tocopherol, chlorophyll, citral *, citronellol *, geraniol *, limonene *, linalool *. * (* Natural constituents of essential oils). HANF-HAARBALSAM Ingredients (INCI): Aqua, Ceteareth-20, Cetearyl Alcohol, Dicocodimonium Chloride, Glycerine, Cannabis Sativa Seed Oil, Coco-Glucoside, Glyceryl Oleate, Natural Perfume, Potassium Sorbate, Panthenol, Citric Acid, Tocopherol, Chlorophyll, Citral *, Citronellol *, geraniol *, limonene *, linalool *. (* natural ingredients of essential oils). Hemp Facial Ingredients (INCI): Aqua, Cannabis Sativa Seed Oil, Cetearyl Alcohol, Cetearyl Glucoside, Sodium Cetearyl Sulfate, Hexyl Decanol, Glycerine, Natural Perfume, Benzyl Alcohol, Potassium Sorbate, Sodium Benzoate, Tocopherol, Panthenol, Citric Acid, Citral * , Citronellol *, geraniol *, limonene *, linalool *. (* natural ingredients of essential oils). HANF HAND CREAM Ingredients (INCI): Cannabis sativa Seed Oil, Cocos Nucifera Oil, Cera Alba, Tocopherol, Natural Perfume, Citral *, Citronellol *, Geraniol *, Limonene *, Linalool *. (* natural ingredients of essential oils). HEMP BODY LOTION INGREDIENTS (INCI): Aqua, Cannabis Sativa Seed Oil, Cetearyl Alcohol, Ceteareth-12, Cetearyl Glucoside, Glycerol, Hexyldecanol, Natural Perfume, Benzyl Alcohol, Potassium Sorbate, Sodium Benzoate, Tocopherol, Panthenol, Citric Acid, Geraniol , Limonene *, linalool *, citronellol *, citral *, (* natural constituents of essential oils). HEMP LIP BALM Ingredients (INCI): Cannabis sativa Seed Oil, Cocos nucifera Oil, Cera Alba, Natural Perfume, Citral *, Citronellol *, Geraniol *, Limonene *, Linalool *. (* natural ingredients of essential oils).

Colors

Designer to choose colors to be used in the design.

Requirements
Must have
• The Sentence: Natural Spirit - Feel the nature should be in front of the label as our slogan for the Cosmetic Line
Should not have
• Hemp leaf

```html
<!DOCTYPE html>
<html lang="de">
<head>
<meta charset="utf-8">
<title>Hanf-Shampoo Etikett</title>
<link rel="stylesheet" href="https://fonts.googleapis.com/css2?family=Arimo&family=Bebas+Neue&family=Dancing+Script:wght@700&family=Montserrat:wght@500&family=Oswald:wght@500&family=Special+Elite&display=swap">
<style>
  :root {
    --bg: #2b1b48;
    --ink: #ffffff;
    --violet: #6d58a3;
    --ornament: #5b4391;
    --rule: #ffffff;
  }
  * { margin: 0; padding: 0; box-sizing: border-box; }
  html, body { width: 1200px; height: 857px; overflow: hidden; background: var(--bg); }
  .label { position: relative; width: 1200px; height: 857px; background: var(--bg); color: var(--ink); overflow: hidden; }
  .ornament { position: absolute; left: 0; top: 0; }
  .brand { position: absolute; left: 263px; top: 108px; width: 282px; text-align: center; }
  .brand-dot { display: block; width: 92px; height: 92px; margin: 0 auto 14px; border-radius: 50%; background: var(--ink); }
  .brand-name { font-family: "Montserrat", sans-serif; font-weight: 500; font-size: 27px; letter-spacing: 1px; white-space: nowrap; }
  .product-title { position: absolute; left: 44px; top: 286px; font-family: "Bebas Neue", sans-serif; font-size: 106px; line-height: 1; letter-spacing: 3px; }
  .title-rule { position: absolute; left: 38px; top: 398px; width: 517px; height: 4px; background: var(--rule); }
  .subtitle { position: absolute; left: 82px; top: 418px; font-family: "Oswald", sans-serif; font-weight: 500; font-size: 20px; letter-spacing: 11.2px; white-space: nowrap; }
  .claims { position: absolute; left: 39px; top: 502px; list-style: none; }
  .claim { position: relative; height: 48px; padding: 10px 0 0 21px; font-family: "Special Elite", monospace; font-size: 19px; font-weight: 700; white-space: nowrap; }
  .claim::before { content: ""; position: absolute; left: 0; top: 0; width: 168px; height: 2px; background: var(--rule); }
  .claim:first-child::before { top: 0; }
  .claim:last-child::before { display: none; }
  .animal-badge { position: absolute; left: 35px; top: 737px; width: 235px; height: 99px; background: var(--violet); padding: 24px 0 0 20px; font-family: "Oswald", sans-serif; font-size: 16px; letter-spacing: 3.2px; line-height: 31px; }
  .maker { position: absolute; left: 296px; top: 754px; font-family: "Oswald", sans-serif; font-size: 16px; letter-spacing: 3.2px; line-height: 41px; }
  .description, .ingredients { position: absolute; left: 698px; width: 470px; font-family: "Arimo", sans-serif; font-size: 19px; line-height: 28.5px; }
  .description { top: 117px; }
  .ingredients { top: 433px; }
  .suitability { position: absolute; left: 698px; top: 300px; width: 470px; font-family: "Dancing Script", cursive; font-size: 22px; line-height: 29px; }
  .suitability .brand-ref { font-family: "Special Elite", monospace; font-size: 18px; }
  .spec-table { position: absolute; left: 669px; top: 740px; width: 495px; height: 117px; border-top: 4px solid var(--rule); }
  .spec-divider { position: absolute; top: 0; width: 4px; height: 117px; background: var(--rule); }
  .spec-volume { position: absolute; left: 29px; top: 30px; font-family: "Bebas Neue", sans-serif; font-size: 46px; white-space: nowrap; }
  .spec-volume small { font-family: "Arimo", sans-serif; font-size: 30px; }
  .spec-estimate { position: absolute; left: 222px; top: 20px; font-family: "Times New Roman", serif; font-size: 52px; }
  .spec-pao { position: absolute; left: 390px; top: 22px; }
</style>
</head>
<body>
<div class="label">
  <svg class="ornament" width="440" height="440" role="img" aria-label="Dekoratives Mandala-Ornament in Violett">
    <defs>
      <radialGradient id="orn" cx="20%" cy="5%" r="90%">
        <stop offset="0" stop-color="#6a51a3" stop-opacity="0.75"/>
        <stop offset="1" stop-color="#3a2760" stop-opacity="0.4"/>
      </radialGradient>
    </defs>
    <circle cx="95" cy="45" r="360" fill="url(#orn)"/>
  </svg>

  <div class="brand">
    <span class="brand-dot"></span>
    <div class="brand-name">BRISK MEADOW</div>
  </div>

  <h1 class="product-title">HANF-SHAMPOO</h1>
  <div class="title-rule"></div>
  <div class="subtitle">BIOLOGISCH ABBAUBAR</div>

  <ul class="claims">
    <li class="claim">OHNE künstliche Farb und Geruchstoffe</li>
    <li class="claim">OHNE Paraffine</li>
    <li class="claim">OHNE Silikone</li>
    <li class="claim">mit reinen Hanfsamenöl</li>
  </ul>

  <div class="animal-badge">PRODUKT NICHT<br>AN TIEREN GETESTET</div>
  <div class="maker">HERSTELLER:<br>MORVIL A-4812 GRUNDLACH</div>

  <p class="description">Hautmilde waschaktive Bestandteile entfalten eine besonders angenehme und schonende Reinigungswirkung. Hochwertiges Hanfsamen-Öl pflegt das Haar auf natürliche Weise und macht es angenehm weich, locker und geschmeidig.</p>

  <p class="suitability"><span class="brand-ref">BRISK MEADOW</span> - eignet sich für alle Haartypen, besonders für strapaziertes und mattes Haar.</p>

  <p class="ingredients">Ingredients (INCI): Aqua, Sodium Laureth Sulfate, TEA-Lauryl Sulfate, Disodium Laureth Sulfosuccinate, Potassium Cocoyl Hydrolized Collagen, Linoleamide-DEA, Cannabis Sativa Seed Oil, Natural Perfume, Sodium Chloride, Citric Acid, Potassium Sorbate, Panthenol, Tocopherol, Chlorophyll, Citral*, Citronellol*, Geraniol*, Limonene*, Linalool*.<br>(* natürliche Bestandteile ätherischer Öle).</p>

  <div class="spec-table">
    <div class="spec-divider" style="left:163px"></div>
    <div class="spec-divider" style="left:332px"></div>
    <div class="spec-volume">200<small>ml</small></div>
    <div class="spec-estimate">e</div>
    <svg class="spec-pao" width="66" height="70" viewBox="0 0 66 70" aria-label="Haltbarkeit nach dem Öffnen 12 Monate">
      <path d="M6 26 L52 4" stroke="#000" stroke-width="6" fill="none"/>
      <path d="M6 26 L52 4" stroke="#fff" stroke-width="3" fill="none"/>
      <rect x="6" y="32" width="54" height="32" rx="4" fill="#fff" stroke="#000" stroke-width="2"/>
      <text x="33" y="55" text-anchor="middle" font-family="Arimo, sans-serif" font-size="15" font-weight="700" fill="#000">12m</text>
    </svg>
  </div>
</div>
</body>
</html>
```